Email Marketing Campaign Brief

We want to do an email marketing campaign around our consulting services. The attached documents provide back ground on our work but additional copy can be found below:

KV7lr is committed to helping you, the educator, make informed buying decisions based on local control and independent reviews through a simple, impartial and an effective approach.
In education, there exists a vast array of educational solutions – such as reading, science, language arts, and math curricula; school-wide reform programs; interventions; after-school programs; and new educational technologies. In the marketplace, providers could, and most do, claim to be able to improve educational outcomes and, in many cases, they all pretend to be supported by evidence. But a cursory review reveals that most evidence consists of poorly designed or advocacy-driven studies with some providers having such inadequate research as could only be described as case studies.

So the problem for State and local education officials is that they must sort through a myriad of such claims to decide which solutions merit consideration for their schools and classrooms. One US official stated the problem saying “many of these practitioners have seen interventions (solutions), introduced with great fanfare as being able to produce dramatic gains, come and go over the years, yielding little in the way of positive and lasting change – a perception confirmed by the flat achievement results over the past 30 years in the Federal Survey of Scholastic Attainment long-term trend”

KV7lr is a process by which we make you, the educator, the locus of control

OUR Approach:
With four simple, yet highly effective steps, KV7lr guides educators through an informed buying process that’s based on local control and review.

Step 1 — Research, Review, and Evaluation Criteria

Step 2 — Cost / Benefit Analysis

Step 3 — Education Survey & Culture Scan

Step 4 — Negotiation & Representation

Target Market(s)

Education

Industry/Entity Type

Marketing

Font styles to use
Sans Serif

Colors
f9b46a
f37122

Requirements
Must have
• HTML format that can be used in an Email Campaign
Nice to have
• Additional Copy in Word

```html
<!DOCTYPE html>
<html lang="en">
<head>
<meta charset="utf-8">
<title>KV7lr Email Campaign</title>
<link href="https://fonts.googleapis.com/css2?family=Open+Sans:wght@400;600;700;800&display=swap" rel="stylesheet">
<style>
:root{
  --orange:#f37122;
  --orange-light:#f9b46a;
  --amber:#f7a21b;
  --green:#8cc63f;
  --green-light:#b9e27a;
  --green-dark:#4f9a2a;
  --ink:#2b2b2b;
  --muted:#555;
  --page:#f2f2f2;
  --white:#fff;
}
*{box-sizing:border-box;margin:0;padding:0}
html,body{width:1200px;height:1200px;overflow:hidden;background:var(--page);font-family:"Open Sans",Arial,sans-serif;color:var(--ink)}
.email{position:absolute;left:272px;top:22px;width:656px;height:1156px;background:var(--white)}
.hero{position:absolute;left:0;top:0;width:656px;height:312px;background:linear-gradient(120deg,#3f7ec9 0%,#8fb6e0 45%,#f4d9b8 75%,#e9e4da 100%)}
.hero-fade{position:absolute;left:0;bottom:0;width:100%;height:70px;background:linear-gradient(to bottom,rgba(255,255,255,0),var(--white))}
.brand-tab{position:absolute;right:50px;top:0;width:160px;height:128px;background:var(--orange);color:var(--white);text-align:center;padding-top:30px}
.brand-name{font-size:28px;font-weight:600;letter-spacing:.5px;display:flex;align-items:center;justify-content:center;gap:8px}
.brand-mark{width:14px;height:14px;background:var(--white);display:inline-block}
.brand-tag{font-size:10px;font-weight:700;margin-top:12px}
.hero-headline{position:absolute;right:30px;top:152px;width:210px;color:var(--white);font-size:27px;font-weight:800;line-height:1.32;text-shadow:0 1px 3px rgba(0,0,0,.35)}
.hero-rule{position:absolute;left:0;top:312px;width:656px;height:4px;background:var(--orange-light)}
.hero-title{position:absolute;left:0;top:318px;width:656px;text-align:center;color:var(--orange);font-size:19px;font-weight:700}
.intro{position:absolute;left:34px;top:354px;width:590px;display:flex;gap:16px;font-size:9.2px;line-height:1.38;color:var(--muted);text-align:justify}
.intro .col{flex:1}
.intro .hl{color:var(--orange);font-weight:700}
.intro h3{font-size:13px;color:var(--ink);font-weight:700;margin:8px 0 1px}
.program{position:absolute;left:0;top:535px;width:656px;height:460px}
.program-head{position:absolute;left:0;top:0;width:656px;height:98px;background:linear-gradient(to bottom,var(--green-dark),var(--green) 45%,var(--green-light));text-align:center;padding-top:46px}
.program-head h2{font-size:17px;font-weight:800;color:#1c2a10}
.program-head p{font-size:11px;font-weight:700;color:#1c2a10}
.row{position:absolute;left:0;width:656px}
.row.orange{background:var(--orange)}
.row.amber{background:linear-gradient(to right,var(--amber),var(--orange-light) 50%,var(--amber))}
.row.green{background:var(--green-light)}
.step{position:absolute;text-align:center;width:270px}
.step-photo{position:absolute;width:250px;height:96px;border:3px solid var(--white)}
.step-num{position:absolute;width:34px;height:34px;border-radius:50%;background:var(--white);border:2px solid var(--orange);color:#d93a1c;font-weight:800;font-size:20px;line-height:30px;text-align:center}
.step h4{font-size:11px;font-weight:800;color:#1c2a10}
.step ul{list-style:none;font-size:7.2px;line-height:1.3;color:#1c2a10}
.cta{position:absolute;left:0;top:1014px;width:656px;text-align:center;font-size:15px;line-height:1.35;color:var(--muted)}
.cta .hl{color:var(--orange);font-weight:700}
.cta strong{display:block;color:var(--ink);font-weight:700}
.footer-bar{position:absolute;left:0;top:1066px;width:656px;height:66px;background:var(--orange);color:var(--white);padding:10px 0 0 34px}
.footer-bar .small{font-size:11px}
.footer-bar .contact{font-size:17px;font-weight:700;margin-top:4px}
.footer-bar .contact span{font-size:13px;margin-right:12px}
.social{position:absolute;right:50px;top:14px;display:flex;gap:8px}
.social i{width:32px;height:32px;border:2px solid var(--white);display:block}
.site{position:absolute;right:64px;top:1138px;font-size:13px;font-weight:700;color:var(--ink)}
</style>
</head>
<body>
<main class="email">
  <section class="hero">
    <div role="img" aria-label="Photo of two smiling schoolgirls leaning over a desk with coloured pencils" style="position:absolute;inset:0"></div>
    <div class="hero-fade"></div>
    <div class="brand-tab">
      <div class="brand-name"><i class="brand-mark"></i>KV7lr</div>
      <div class="brand-tag">Research + Policy + Practice</div>
    </div>
    <p class="hero-headline">We help you to build geniuses</p>
  </section>
  <div class="hero-rule"></div>
  <h1 class="hero-title">Research, Teaching, Learning</h1>

  <section class="intro">
    <div class="col">
      <p>According to the Allied Council of School Leaders, our K12 education system has over $200 billion of annual spending power. Of that amount, an estimated $8 billion is spent by educators on products and services with the hope of an output that produces positive results for children. But with that come thousands of for-profit and not-for-profit providers that market thousands of learning solutions to administrators, superintendents, and principals who make these buying decisions. The estimated 3 million teachers are left to wonder where these solutions come from, whether they are the best for their learners, and whether, ultimately, they will make a difference to teaching and learning.</p>
    </div>
    <div class="col">
      <p>KV7lr takes apart the provider-led reviews and long drawn out process of selecting a program solution and puts you in the drivers seat. From cultural scan to educator and community surveys, we help you make an informed, independent review and selection that's right for your students, teachers and administrators. <span class="hl">KV7lr</span> is a process by which we make you, the educator, the focus of control.</p>
      <h3>OUR Approach:</h3>
      <p>With four simple, yet highly effective steps, KV7lr guides educators through an informed buying process that's based on local control and review.</p>
    </div>
  </section>

  <section class="program">
    <header class="program-head">
      <h2>PROGRAM IMPLEMENTATION</h2>
      <p>Independent Review Connected to School District Need and Stakeholder</p>
    </header>

    <div class="row orange" style="top:98px;height:124px"></div>
    <div class="row green" style="top:222px;height:66px"></div>
    <div class="row amber" style="top:288px;height:118px"></div>
    <div class="row green" style="top:406px;height:54px;background:linear-gradient(var(--green-light),var(--white))"></div>

    <div class="step-photo" role="img" aria-label="Photo of children reading together" style="left:66px;top:112px;background:linear-gradient(135deg,#7fb3d9,#e9c9a4 60%,#6aa3cf)"></div>
    <div class="step-photo" role="img" aria-label="Photo of printed charts and graphs" style="left:340px;top:112px;background:linear-gradient(135deg,#f4f4f4,#d9dde6 55%,#c7a9a0)"></div>
    <div class="step-num" style="left:174px;top:192px">1</div>
    <div class="step-num" style="left:448px;top:192px">2</div>

    <div class="step" style="left:56px;top:232px">
      <h4>Research, Review, and Evaluation Criteria</h4>
      <ul><li>* District needs analysis</li><li>* Program reviews and alignment to need</li><li>* Independent evaluation / data informed decisions</li></ul>
    </div>
    <div class="step" style="left:330px;top:232px">
      <h4>Cost / Benefit Analysis</h4>
      <ul><li>* Cost alignment based on research and evaluation of programs</li><li>* Program cost by product offering and alignment to needs</li><li>* Survey of cost, data and return on investment</li></ul>
    </div>

    <div class="step-photo" role="img" aria-label="Photo of a hand signing a document" style="left:66px;top:292px;background:linear-gradient(135deg,#e7e3dd,#9a8f86 60%,#3a3532)"></div>
    <div class="step-photo" role="img" aria-label="Photo of two people shaking hands across a desk" style="left:340px;top:292px;background:linear-gradient(135deg,#cfc8be,#8a7566 55%,#e2ddd5)"></div>
    <div class="step-num" style="left:174px;top:372px">3</div>
    <div class="step-num" style="left:448px;top:372px">4</div>

    <div class="step" style="left:56px;top:414px">
      <h4>Education Survey and Culture Scan</h4>
      <ul><li>* District observation and perception survey</li><li>* Culture scan to identify education best practices</li><li>* Match to strategic plan goals and objectives</li></ul>
    </div>
    <div class="step" style="left:330px;top:414px">
      <h4>Negotiation and Representation</h4>
      <ul><li>* Contact provider review and presentation</li><li>* Representation for content and program negotiations</li><li>* Support district in independent decision-making process</li></ul>
    </div>
  </section>

  <p class="cta">Let <span class="hl">KV7lr</span> help you make informed buying decisions.<strong>Contact us today for a no-cost consultation</strong></p>

  <footer class="footer-bar">
    <p class="small">Let's get connected!</p>
    <p class="contact"><span>KV7lr, LLC</span>555.010.0199</p>
    <div class="social" aria-label="Social links"><i></i><i></i><i></i><i></i></div>
  </footer>
  <p class="site">www.kv7lr.example</p>
</main>
</body>
</html>
```